We are an import/export consulting business dealing with all aspects of import/export regulations. Our current design if you look at our website (www.morvelin.com) are different country flags. It is our business to stay up to date on laws and regulations. We assist companies worldwide. We would like to keep with the flag theme but something different or maybe someone can come up with something totally different that would capture our attention. We are open to suggestions. This design then will transfer over to letterhead, our website, marketing brochures, etc.

Lorraine B. Morvelin, President
Morvelin Global Advisors, LLC
7 Birchfield Lane,
Ashbury, VT 05412

```html
<!DOCTYPE html>
<html lang="en">
<head>
<meta charset="utf-8">
<title>Morvelin Global Advisors – Business Card</title>
<link href="https://fonts.googleapis.com/css2?family=Open+Sans:wght@400;600;700&display=swap" rel="stylesheet">
<style>
  :root{
    --navy:#111a3a;
    --red:#a71e23;
    --gold:#d4a92a;
    --lime:#cfc72a;
    --white:#ffffff;
    --paper:#f6f7f9;
    --bg:#e9e7e3;
    --flag-a:#c43b3b;
    --flag-b:#2f4f9a;
  }
  *{box-sizing:border-box;margin:0;padding:0}
  html,body{width:1200px;height:1000px;overflow:hidden;background:var(--bg);font-family:"Open Sans",Arial,sans-serif}
  .canvas{position:relative;width:1200px;height:1000px}
  .card{position:absolute;left:285px;width:630px;height:360px;box-shadow:0 6px 18px rgba(0,0,0,.18)}
  .card--front{top:70px;background:var(--red);padding:16px}
  .front-navy{width:100%;height:100%;background:var(--navy);padding:10px}
  .front-gold{width:100%;height:100%;background:var(--gold);padding:10px}
  .front-panel{width:100%;height:100%;background:var(--white);display:flex;flex-direction:column;align-items:center;justify-content:center;gap:36px}
  .brand{display:flex;align-items:center;gap:14px;color:var(--navy);font-weight:700}
  .brand__dot{flex:none;border-radius:50%;background:var(--navy)}
  .brand__name{line-height:1.05;text-transform:uppercase;letter-spacing:.5px;white-space:nowrap}
  .brand--large .brand__dot{width:70px;height:70px}
  .brand--large .brand__name{font-size:30px}
  .brand--small .brand__dot{width:46px;height:46px}
  .brand--small .brand__name{font-size:17px}
  .flag-strip{height:14px;background:linear-gradient(90deg,var(--flag-a),var(--white) 20%,var(--flag-b) 40%,var(--white) 55%,var(--flag-a) 75%,var(--flag-b))}
  .flag-strip--front{width:220px}
  .flag-strip--back{width:200px;position:absolute;right:50px;top:100px}

  .card--back{top:560px;background:var(--paper);overflow:hidden}
  .card--back .brand{position:absolute;left:50px;top:60px}
  .back-waves{position:absolute;left:0;top:0;width:630px;height:360px}
  .contact{position:absolute;left:0;right:0;top:218px;color:var(--white);text-align:center}
  .contact__name{font-size:21px;font-weight:700}
  .contact__role{font-size:14px;font-weight:400}
  .contact__company{font-size:16px;font-weight:600;margin-top:2px}
  .contact__address{font-size:13px;margin-top:2px}
  .contact__row{display:flex;justify-content:center;gap:38px;font-size:13px;margin-top:18px}
  .contact__row span,.contact__address{display:inline-flex;align-items:center;gap:6px}
  .icon{width:12px;height:12px;fill:var(--white)}
</style>
</head>
<body>
<main class="canvas">

  <section class="card card--front" aria-label="Business card front">
    <div class="front-navy"><div class="front-gold"><div class="front-panel">
      <div class="brand brand--large">
        <span class="brand__dot"></span>
        <span class="brand__name">Morvelin<br>Global Advisors, LLC</span>
      </div>
      <div class="flag-strip flag-strip--front" role="img" aria-label="Row of small country flags"></div>
    </div></div></div>
  </section>

  <section class="card card--back" aria-label="Business card back">
    <svg class="back-waves" viewBox="0 0 630 360" preserveAspectRatio="none" aria-hidden="true">
      <path d="M0 150 Q320 185 630 165 L630 360 L0 360Z" fill="var(--lime)"/>
      <path d="M0 162 Q320 200 630 195 L630 360 L0 360Z" fill="var(--red)"/>
      <path d="M0 175 Q320 215 630 228 L630 360 L0 360Z" fill="var(--navy)"/>
    </svg>

    <div class="brand brand--small">
      <span class="brand__dot"></span>
      <span class="brand__name">Morvelin<br>Global Advisors, LLC</span>
    </div>
    <div class="flag-strip flag-strip--back" role="img" aria-label="Row of small country flags"></div>

    <div class="contact">
      <p class="contact__name">Lorraine B. Morvelin | <span class="contact__role">President</span></p>
      <p class="contact__company">Morvelin Global Advisors, LLC</p>
      <p class="contact__address">
        <svg class="icon" viewBox="0 0 12 12"><path d="M6 1 L11 6 H9.5 V11 H7 V8 H5 V11 H2.5 V6 H1Z"/></svg>
        7 Birchfield Lane, Ashbury, VT 05412
      </p>
      <div class="contact__row">
        <span><svg class="icon" viewBox="0 0 12 12"><path d="M2 1h3l1 3-1.5 1a7 7 0 0 0 2.5 2.5L8 6l3 1v3c0 .6-.4 1-1 1A9 9 0 0 1 1 2c0-.6.4-1 1-1z"/></svg>802-555-0147</span>
        <span><svg class="icon" viewBox="0 0 12 12"><path d="M1 3h10v6H1z M1 3l5 4 5-4" fill="none" stroke="#fff" stroke-width="1.2"/></svg>lorraine@morvelin.com</span>
        <span><svg class="icon" viewBox="0 0 12 12"><path d="M4 8l4-4M3 6L1.5 7.5a2 2 0 0 0 3 3L6 9M9 6l1.5-1.5a2 2 0 0 0-3-3L6 3" fill="none" stroke="#fff" stroke-width="1.2"/></svg>www.morvelin.com</span>
      </div>
    </div>
  </section>

</main>
</body>
</html>
```